Corvy

Electronic Repairs for OEM's Industrial electronic repairs, consumer audio visual, Projectors

Target Market(s)

manufacturer of electronics (OEM), business, Government, then Consumer

Industry/Entity Type

Electronic Repair

Contact Information for Business Card

Board Repair, Projectors

Font styles to use
Serif

Colors
0054AA
0677BA
7BADD7
CADEEF
E8F1F8

Requirements
Must have
• projector, led wall image
Nice to have
• professional looking business card.
Should not have
• unsure

```html
<!DOCTYPE html>
<html lang="en">
<head>
<meta charset="utf-8">
<title>Corvy Electronic Repairs – Business Card</title>
<link rel="stylesheet" href="https://fonts.googleapis.com/css2?family=Montserrat:wght@400;600&family=Oswald:wght@500;600&family=Roboto+Condensed:ital,wght@0,400;0,700;1,700&display=swap">
<style>
  :root {
    --blue-deep: #0054aa;
    --blue-mid: #0677ba;
    --blue-soft: #7badd7;
    --blue-pale: #cadeef;
    --blue-mist: #e8f1f8;
    --ink: #1b1b1b;
    --paper: #ffffff;
    --backdrop: #e4e2de;
  }
  * { margin: 0; padding: 0; box-sizing: border-box; }
  html, body {
    width: 1200px; height: 969px; overflow: hidden;
    background: var(--backdrop);
  }
  .card {
    position: absolute; left: 50px; top: 172px;
    width: 1170px; height: 665px;
    transform: scale(0.9402); transform-origin: 0 0;
    background: var(--paper);
    border-radius: 28px;
    overflow: hidden;
    box-shadow: 0 10px 30px rgba(0,0,0,.18);
  }
  .brand { position: absolute; left: 72px; top: 54px; }
  .brand-mark {
    position: absolute; left: 0; top: 0;
    width: 122px; height: 122px; border-radius: 50%;
    background: var(--blue-deep);
  }
  .brand-name {
    position: absolute; left: 140px; top: -12px;
    font: 600 104px/1 "Montserrat", sans-serif;
    color: var(--blue-deep); letter-spacing: -2px;
  }
  .brand-sub {
    position: absolute; left: 143px; top: 90px; white-space: nowrap;
    font: 400 31px/1 "Montserrat", sans-serif;
    color: var(--blue-mid); letter-spacing: 0.5px;
  }
  .services {
    position: absolute; left: 613px; top: 60px;
    font: 600 33px/37px "Oswald", sans-serif;
    color: var(--blue-deep); text-transform: uppercase;
    letter-spacing: -0.3px;
  }
  .gallery {
    position: absolute; left: 0; top: 238px; width: 1170px; height: 322px;
    display: grid; grid-template-columns: 407px 367px 396px;
  }
  .tile { display: flex; flex-direction: column; }
  .tile-photo { flex: 1; }
  .tile--projector .tile-photo {
    background: radial-gradient(circle at 22% 48%, #c9d6f0 0%, #4f9fc0 14%, #2f87a6 40%, #1d5f7c 100%);
  }
  .tile--ledwall .tile-photo {
    background: linear-gradient(90deg, #ffffff 0%, #d9dcdf 12%, #ffffff 50%, #d9dcdf 62%, #ffffff 100%);
  }
  .tile--board .tile-photo {
    background: radial-gradient(circle at 55% 55%, #7fb0dc 0%, #2f6fae 35%, #143f78 75%, #0c2b55 100%);
  }
  .tile-caption {
    height: 54px; display: flex; align-items: center; justify-content: center;
    font: 500 32px/1 "Oswald", sans-serif; color: #fff; text-transform: uppercase;
  }
  .tile--projector .tile-caption { background: #2468bb; }
  .tile--ledwall .tile-caption { background: #3289cf; }
  .tile--board .tile-caption { background: var(--blue-deep); }
  .contact {
    position: absolute; left: 68px; top: 594px; white-space: nowrap;
    font: 400 36px/1 "Roboto Condensed", sans-serif;
  }
  .contact-label { color: var(--blue-mid); }
  .contact-phone { color: var(--ink); font-weight: 700; margin-right: 28px; }
  .contact-email { color: var(--ink); font-weight: 700; font-style: italic; }
</style>
</head>
<body>
  <div class="card">
    <div class="brand">
      <div class="brand-mark"></div>
      <div class="brand-name">CORVY</div>
      <div class="brand-sub">ELECTRONIC REPAIRS</div>
    </div>
    <div class="services">
      Electronic repairs for<br>
      OEM's industrial electronic repairs<br>
      Consumer audio visual, projectors
    </div>
    <div class="gallery">
      <div class="tile tile--projector">
        <div class="tile-photo" role="img" aria-label="Photo: hands adjusting a ceiling-mounted projector with its lamp glowing, in a blue-lit room with blinds"></div>
        <div class="tile-caption">Projector</div>
      </div>
      <div class="tile tile--ledwall">
        <div class="tile-photo" role="img" aria-label="Photo: two free-standing LED wall display frames with grey panels on silver metal posts"></div>
        <div class="tile-caption">LED Wall Image</div>
      </div>
      <div class="tile tile--board">
        <div class="tile-photo" role="img" aria-label="Photo: steel tweezers placing a component on a blue printed circuit board"></div>
        <div class="tile-caption">Board Repair</div>
      </div>
    </div>
    <div class="contact">
      <span class="contact-label">CALL US</span>
      <span class="contact-phone">555-014-2287</span>
      <span class="contact-label">EMAIL US</span>
      <span class="contact-email">info@corvyelectronicrepairs.com</span>
    </div>
  </div>
</body>
</html>
```